Business Card for a New Zealand IT Startup

I need a business card for VELTA Holdings. We are a young startup based in New Zealand working in internet marketing and web development. The design should have some element connected to New Zealand, such as wave, koru or silver fern, just don't use a kiwi bird.

```html
<!DOCTYPE html>
<html lang="en">
<head>
<meta charset="utf-8">
<title>VELTA Holdings – Business Card</title>
<link rel="stylesheet" href="https://fonts.googleapis.com/css2?family=Open+Sans:wght@400;600;700&display=swap">
<style>
  :root{
    --page-bg:#e9e7e4;
    --panel-white:#f4f5f6;
    --brand-blue:#2472b3;
    --brand-orange:#d4582a;
    --grad-blue:#2f6fae;
    --grad-grey:#77777c;
    --grad-orange:#c4562c;
    --text-light:#ede3d6;
    --text-soft:#e2d9cf;
  }
  html,body{margin:0;padding:0;width:1200px;height:1054px;overflow:hidden;background:var(--page-bg);}
  .canvas{position:relative;width:1200px;height:1054px;}
  .card{
    position:absolute;left:100px;top:237px;width:1000px;height:580px;
    overflow:hidden;border-radius:4px;
    background:linear-gradient(30deg,var(--grad-orange) 0%,#9a6552 30%,var(--grad-grey) 55%,#5f7288 75%,var(--grad-blue) 100%);
    box-shadow:0 10px 30px rgba(0,0,0,.18);
  }
  .card__shape{position:absolute;inset:0;width:1000px;height:580px;}
  .brand{
    position:absolute;left:128px;top:0;height:580px;width:80px;
    display:flex;flex-direction:column;align-items:center;justify-content:center;gap:16px;
  }
  .brand__mark{width:24px;height:24px;border-radius:50%;background:var(--brand-blue);flex:none;}
  .brand__name{
    writing-mode:vertical-rl;transform:rotate(180deg);
    font-family:"Open Sans",sans-serif;font-weight:700;font-size:34px;
    letter-spacing:5px;color:var(--brand-blue);white-space:nowrap;line-height:1;
  }
  .details{position:absolute;left:522px;top:140px;color:var(--text-light);font-family:"Open Sans",sans-serif;}
  .details__name{font-weight:600;font-size:37px;margin:0;letter-spacing:.3px;}
  .details__title{font-size:21px;margin:2px 0 0;color:var(--text-soft);}
  .details__address{font-size:21px;line-height:32px;margin:56px 0 0;color:var(--text-soft);}
  .contacts{list-style:none;margin:20px 0 0;padding:0;}
  .contacts__item{display:flex;align-items:center;gap:24px;font-size:21px;line-height:35px;color:var(--text-soft);}
  .contacts__icon{width:22px;height:22px;flex:none;}
</style>
</head>
<body>
<div class="canvas">
  <section class="card" aria-label="VELTA Holdings business card">
    <svg class="card__shape" viewBox="0 0 1000 580" aria-hidden="true">
      <defs>
        <linearGradient id="edgeStroke" x1="0" y1="0" x2="0" y2="1">
          <stop offset="0" stop-color="#2472b3"/>
          <stop offset="0.55" stop-color="#2c5f95"/>
          <stop offset="1" stop-color="#d4582a"/>
        </linearGradient>
      </defs>
      <path class="card__wave-panel" d="M0 0 H362 C415 130 380 250 400 340 C418 420 360 520 322 580 H0 Z" fill="var(--panel-white)"/>
      <path class="card__wave-edge" d="M362 0 C415 130 380 250 400 340 C418 420 360 520 322 580" fill="none" stroke="url(#edgeStroke)" stroke-width="9"/>
    </svg>

    <div class="brand">
      <span class="brand__mark"></span>
      <span class="brand__name">VELTA HOLDINGS</span>
    </div>

    <div class="details">
      <h1 class="details__name">Liam Parker Reid</h1>
      <p class="details__title">Managing Director</p>
      <p class="details__address">48 Harbour Lane, Kauri Bay,<br>Wellington, NZ 6011</p>
      <ul class="contacts">
        <li class="contacts__item">
          <svg class="contacts__icon" viewBox="0 0 24 24" aria-hidden="true"><path fill="currentColor" d="M3 8c0-2 3-4 9-4s9 2 9 4v2h-5V8H8v2H3zM6 11h12l2 9H4z"/><circle cx="12" cy="15" r="2.2" fill="#8a7a70"/></svg>
          <span>021-4455-870</span>
        </li>
        <li class="contacts__item">
          <svg class="contacts__icon" viewBox="0 0 24 24" aria-hidden="true"><rect x="3" y="6" width="18" height="12" fill="currentColor"/><path d="M3 6l9 7 9-7" fill="none" stroke="#7b7078" stroke-width="1.6"/></svg>
          <span>hello@veltaholdings.com</span>
        </li>
        <li class="contacts__item">
          <svg class="contacts__icon" viewBox="0 0 24 24" aria-hidden="true"><g fill="none" stroke="currentColor" stroke-width="1.8"><circle cx="12" cy="12" r="8.5"/><ellipse cx="12" cy="12" rx="3.8" ry="8.5"/><path d="M3.5 12h17M5 7.5h14M5 16.5h14"/></g></svg>
          <span>www.veltaholdings.com</span>
        </li>
      </ul>
    </div>
  </section>
</div>
</body>
</html>
```